Thornbury Building Company - Card Design

I am looking to use the logo designs that you already did for me to develop a business card. I would like the card to have a black background and be double sided. I want white and green logo and text. I have attached an inspiration photo of a look that I like. I would like to use the Vertical Logo attached to take up the full front side of the card. On the back where I have my name and information, I would like to have the horizontal logo or maybe even just the image of the 'A' and trees without the text. I am open, but I am looking for something clean and simple and I want the green to really pop! Additional files can be found under Design #: 58302946

Target Market(s)

Homeowners

Industry/Entity Type

Construction

Contact Information for Business Card

Name: Marcus Thornbury, Title: Project Manager, Phone: 555.274.8136, Email: thornburybuildingcompany@mailvesta.com, address: 487 Larkspur Ln, Cedar Hollow, NV 95033, Lic# 2468317

Colors
00AB8E
00BBA5
67D7C9
C6EFE9
E9F9F6

Requirements
Nice to have
• I would like to see the logos that I have already got from ArtLoomHub, though I am open to new ones

```html
<!DOCTYPE html>
<html lang="en">
<head>
<meta charset="utf-8">
<title>Thornbury Building Company – Business Card</title>
<link rel="stylesheet" href="https://fonts.googleapis.com/css2?family=Montserrat:wght@400;500;700&display=swap">
<style>
  :root {
    --backdrop: #3b3b3b;
    --card: #1f1f1f;
    --green: #3cbf3c;
    --white: #ffffff;
    --muted: #e6e6e6;
  }
  * { margin: 0; padding: 0; box-sizing: border-box; }
  html, body {
    width: 1200px; height: 1200px; overflow: hidden;
    background: var(--backdrop);
    font-family: "Montserrat", sans-serif;
  }
  .canvas { position: relative; width: 1200px; height: 1200px; }

  .card {
    position: absolute;
    width: 760px; height: 434px;
    background: var(--card);
    border-radius: 32px;
    box-shadow: 0 18px 40px rgba(0,0,0,.45);
    overflow: hidden;
  }
  .card--back { left: 110px; top: 150px; }
  .card--front { left: 330px; top: 640px; }

  /* Back side: brand + contact */
  .brand-mark {
    position: absolute; left: 50px; top: 150px; width: 290px;
    display: flex; align-items: center; gap: 14px;
  }
  .brand-dot {
    flex: none; width: 34px; height: 34px; border-radius: 50%;
    background: var(--green);
  }
  .brand-name {
    color: var(--white); font-weight: 700; font-size: 25px;
    line-height: 1.15; letter-spacing: .02em; text-transform: uppercase;
  }

  .contact { position: absolute; left: 370px; top: 110px; width: 360px; }
  .contact__name {
    color: var(--green); font-weight: 700; font-size: 26px;
    letter-spacing: .01em; text-transform: uppercase; line-height: 1.1;
  }
  .contact__title {
    color: var(--white); font-weight: 500; font-size: 15px;
    text-transform: uppercase; margin-bottom: 22px;
  }
  .contact__list { list-style: none; }
  .contact__item {
    display: flex; align-items: center; gap: 10px;
    color: var(--muted); font-size: 14px; line-height: 1.25;
    margin-bottom: 10px; white-space: nowrap;
  }
  .contact__item svg { flex: none; width: 18px; height: 18px; fill: var(--green); }
  .contact__item--plain { padding-left: 28px; }

  .accent-bar {
    position: absolute; left: 330px; bottom: 0;
    width: 300px; height: 24px; background: var(--green);
  }

  /* Front side: centered brand */
  .emblem {
    position: absolute; left: 50%; top: 50%;
    width: 320px; height: 320px; transform: translate(-50%, -50%);
    border: 9px solid var(--white); border-radius: 50%;
    display: flex; align-items: center; justify-content: center;
  }
  .emblem__name {
    color: var(--white); font-weight: 700; font-size: 34px;
    line-height: 1.15; text-align: center; text-transform: uppercase;
    letter-spacing: .02em;
  }
</style>
</head>
<body>
<main class="canvas">
  <section class="card card--back" aria-label="Card back with contact details">
    <div class="brand-mark">
      <span class="brand-dot"></span>
      <span class="brand-name">Thornbury Building Company</span>
    </div>

    <div class="contact">
      <p class="contact__name">Marcus Thornbury</p>
      <p class="contact__title">Project Manager</p>
      <ul class="contact__list">
        <li class="contact__item">
          <svg viewBox="0 0 24 24"><path d="M6.6 10.8a15.1 15.1 0 0 0 6.6 6.6l2.2-2.2c.3-.3.7-.4 1-.2 1.1.4 2.3.6 3.6.6.6 0 1 .4 1 1V20c0 .6-.4 1-1 1C10.6 21 3 13.4 3 4c0-.6.4-1 1-1h3.5c.6 0 1 .4 1 1 0 1.3.2 2.5.6 3.6.1.3 0 .7-.2 1z"/></svg>
          555.274.8136
        </li>
        <li class="contact__item">
          <svg viewBox="0 0 24 24"><path d="M2 5h20v2l-10 7L2 7z"/><path d="M2 8l7 5-7 6zM22 8l-7 5 7 6zM10 14l2 1.4 2-1.4 7 5H3z"/></svg>
          thornburybuildingcompany@mailvesta.com
        </li>
        <li class="contact__item">
          <svg viewBox="0 0 24 24"><path d="M12 2a7 7 0 0 0-7 7c0 5.2 7 13 7 13s7-7.8 7-13a7 7 0 0 0-7-7zm0 9.5A2.5 2.5 0 1 1 12 6.5a2.5 2.5 0 0 1 0 5z"/></svg>
          487 Larkspur Ln, Cedar Hollow, NV 95033
        </li>
        <li class="contact__item contact__item--plain">Lic# 2468317</li>
      </ul>
    </div>

    <div class="accent-bar"></div>
  </section>

  <section class="card card--front" aria-label="Card front with brand">
    <div class="emblem">
      <span class="emblem__name">Thornbury<br>Building<br>Company</span>
    </div>
  </section>
</main>
</body>
</html>
```